Velquist Capital LLC

Need Professional Business cards for New Investment Fund

Target Market(s)

High Quality investors

Industry/Entity Type

Financial

Contact Information for Business Card

Phone Number +1 555 284 6190
Name Lukas Varenko
Title Fund Manager
email lv@FundVelquist.com
Website www.FundVelquist.com

Colors

Designer to choose colors to be used in the design.

Requirements
Must have
• Must have our Logo and all of the above. Must be made so lettering and loge can be raised

```html
<!DOCTYPE html>
<html lang="en">
<head>
<meta charset="utf-8">
<title>Velquist Capital – Business Card</title>
<link rel="stylesheet" href="https://fonts.googleapis.com/css2?family=Jost:wght@400;600&family=Lato:wght@400&display=swap">
<style>
  :root {
    --backdrop: #8a5a32;
    --kraft-light: #dcbd90;
    --kraft-mid: #c7a06c;
    --kraft-dark: #ad824e;
    --ink: #111111;
  }
  * { margin: 0; padding: 0; box-sizing: border-box; }
  html, body { width: 1200px; height: 900px; overflow: hidden; }
  body { background: var(--backdrop); position: relative; }

  .card {
    position: absolute;
    background: linear-gradient(160deg, var(--kraft-light) 0%, var(--kraft-mid) 55%, var(--kraft-dark) 100%);
    color: var(--ink);
  }
  .card--front { left: 330px; top: 90px; width: 555px; height: 343px; }
  .card--back  { left: 330px; top: 470px; width: 558px; height: 342px; }

  .holder {
    position: absolute; left: 0; right: 0; top: 98px;
    text-align: center;
  }
  .holder__name {
    font-family: "Jost", sans-serif; font-weight: 600;
    font-size: 20px; letter-spacing: 0.5px; line-height: 24px;
  }
  .holder__title {
    font-family: "Lato", sans-serif; font-size: 15px; line-height: 16px;
  }

  .contact-divider {
    position: absolute; left: 187px; top: 148px;
  }

  .contact-list {
    position: absolute; left: 0; right: 0; top: 183px;
    list-style: none; text-align: center;
    font-family: "Lato", sans-serif; font-size: 15px; line-height: 20px;
  }

  .brand {
    position: absolute; left: 0; right: 0; top: 150px;
    display: flex; justify-content: center; align-items: center; gap: 12px;
  }
  .brand__square { width: 16px; height: 16px; background: var(--ink); }
  .brand__name {
    font-family: "Jost", sans-serif; font-weight: 600;
    font-size: 34px; letter-spacing: 4px; text-transform: uppercase;
  }
</style>
</head>
<body>
  <section class="card card--front">
    <div class="holder">
      <h1 class="holder__name">LUKAS VARENKO</h1>
      <p class="holder__title">Fund Manager</p>
    </div>

    <svg class="contact-divider" width="180" height="24" viewBox="0 0 180 24" aria-hidden="true">
      <line x1="0" y1="12" x2="52" y2="12" stroke="#111" stroke-width="1"/>
      <line x1="128" y1="12" x2="180" y2="12" stroke="#111" stroke-width="1"/>
      <circle cx="64" cy="12" r="11" fill="#111"/>
      <path d="M58 10 q6 -5 12 0 l-2 2 h-2 l-1 -2 h-2 l-1 2 h-2 z M59 14 h10 v4 h-10 z" fill="#d2ad7a"/>
      <circle cx="90" cy="12" r="11" fill="#111"/>
      <rect x="83" y="7.5" width="14" height="9" fill="#d2ad7a"/>
      <path d="M83 7.5 l7 5 l7 -5" fill="none" stroke="#111" stroke-width="1.3"/>
      <circle cx="116" cy="12" r="11" fill="#111"/>
      <circle cx="116" cy="12" r="6.5" fill="#d2ad7a"/>
      <path d="M116 5.5 v13 M109.5 12 h13 M116 5.5 q-4 6.5 0 13 M116 5.5 q4 6.5 0 13" fill="none" stroke="#111" stroke-width="1"/>
    </svg>

    <ul class="contact-list">
      <li>+1 555 284 6190</li>
      <li>lv@FundVelquist.com</li>
      <li>www.FundVelquist.com</li>
    </ul>
  </section>

  <section class="card card--back">
    <div class="brand">
      <span class="brand__square"></span>
      <span class="brand__name">Velquist</span>
    </div>
  </section>
</body>
</html>
```